Business Card Design (NEW FILES)

ATTENTION: New vector files are available. Please update your design to reflect/use the new (better resolution) logo images.

Seeking a unique and professional business card design for a commercial drone photography/videography business. The layout should feature
the logo (attached) and include the following information:
Owen Tarrick
614-502-7738
www.skylarkreelworks.example
NRD Certified Remote Pilot

Owen Tarrick

```html
<!DOCTYPE html>
<html lang="en">
<head>
<meta charset="utf-8">
<title>Skylark Reelworks – Business Card</title>
<link rel="stylesheet" href="https://fonts.googleapis.com/css2?family=Montserrat:wght@300;400;600;700&display=swap">
<style>
  :root {
    --stage: #2a2a2c;
    --navy: #141a48;
    --orange: #ef8a4b;
    --white: #ffffff;
    --ink-soft: #1d2355;
  }
  * { margin: 0; padding: 0; box-sizing: border-box; }
  html, body {
    width: 1200px;
    height: 875px;
    overflow: hidden;
    background: var(--stage);
    font-family: "Montserrat", sans-serif;
  }
  .canvas {
    position: relative;
    width: 1200px;
    height: 875px;
  }
  .card {
    position: absolute;
    width: 530px;
    height: 303px;
    border-radius: 18px;
    overflow: hidden;
  }

  /* Front */
  .card-front {
    left: 70px;
    top: 140px;
    background: var(--navy);
    display: flex;
    flex-direction: column;
    align-items: center;
    justify-content: center;
    gap: 16px;
  }
  .brand {
    display: flex;
    align-items: center;
    gap: 14px;
  }
  .brand-dot {
    width: 22px;
    height: 22px;
    border-radius: 50%;
    background: var(--orange);
  }
  .brand-name {
    color: var(--white);
    font-weight: 300;
    font-size: 34px;
    letter-spacing: 3px;
    text-transform: uppercase;
  }
  .tagline {
    color: var(--orange);
    font-weight: 400;
    font-size: 14px;
    letter-spacing: 3px;
    text-transform: uppercase;
  }

  /* Back */
  .card-back {
    left: 600px;
    top: 430px;
    background: var(--white);
    padding: 30px 34px;
  }
  .back-brand {
    display: flex;
    align-items: center;
    gap: 10px;
  }
  .back-brand .brand-dot { width: 16px; height: 16px; }
  .back-brand .brand-name {
    color: var(--navy);
    font-size: 20px;
    font-weight: 300;
    letter-spacing: 2px;
  }
  .contact {
    position: absolute;
    right: 34px;
    top: 100px;
    list-style: none;
    display: flex;
    flex-direction: column;
    gap: 8px;
  }
  .contact li {
    display: flex;
    align-items: center;
    gap: 8px;
    color: var(--ink-soft);
  }
  .contact .phone { font-weight: 600; font-size: 17px; letter-spacing: 0.5px; }
  .contact .web { font-weight: 400; font-size: 12.5px; }
  .contact svg { width: 13px; height: 13px; flex: none; }
  .person {
    position: absolute;
    left: 34px;
    top: 160px;
  }
  .person-name {
    color: var(--navy);
    font-weight: 700;
    font-size: 24px;
    letter-spacing: 0.5px;
    text-transform: uppercase;
  }
  .person-role {
    color: var(--orange);
    font-weight: 400;
    font-size: 15px;
  }
  .credentials {
    position: absolute;
    left: 34px;
    bottom: 26px;
  }
  .certification {
    color: var(--orange);
    font-weight: 700;
    font-size: 18px;
    text-transform: uppercase;
    letter-spacing: 0.5px;
  }
  .insured {
    color: var(--navy);
    font-weight: 600;
    font-size: 12px;
    letter-spacing: 1.5px;
    text-transform: uppercase;
    margin-top: 2px;
  }
</style>
</head>
<body>
<main class="canvas">
  <section class="card card-front" aria-label="Card front">
    <div class="brand">
      <span class="brand-dot"></span>
      <span class="brand-name">Skylark Reelworks</span>
    </div>
    <p class="tagline">Captivating Aerial Imagery</p>
  </section>

  <section class="card card-back" aria-label="Card back">
    <div class="back-brand">
      <span class="brand-dot"></span>
      <span class="brand-name">Skylark Reelworks</span>
    </div>

    <ul class="contact">
      <li class="phone">
        <svg viewBox="0 0 24 24" aria-hidden="true"><path fill="#ef8a4b" d="M6.6 10.8a15.1 15.1 0 0 0 6.6 6.6l2.2-2.2c.3-.3.7-.4 1-.2 1.1.4 2.3.6 3.6.6.6 0 1 .4 1 1V20c0 .6-.4 1-1 1A17 17 0 0 1 3 4c0-.6.4-1 1-1h3.5c.6 0 1 .4 1 1 0 1.3.2 2.5.6 3.6.1.3 0 .7-.2 1z"/></svg>
        614-502-7738
      </li>
      <li class="web">
        <svg viewBox="0 0 24 24" aria-hidden="true"><circle cx="12" cy="12" r="10" fill="none" stroke="#ef8a4b" stroke-width="2.4"/><path d="M2 12h20M12 2c3 3 3 17 0 20M12 2c-3 3-3 17 0 20" fill="none" stroke="#ef8a4b" stroke-width="1.8"/></svg>
        www.skylarkreelworks.example
      </li>
    </ul>

    <div class="person">
      <p class="person-name">Owen Tarrick</p>
      <p class="person-role">Owner</p>
    </div>

    <div class="credentials">
      <p class="certification">NRD Certified Remote Pilot</p>
      <p class="insured">Fully Insured</p>
    </div>
  </section>
</main>
</body>
</html>
```